Locksmith Business Cards

My father-in-law is in need of new business cards for his locksmith business and I need to impress him. Kindly help me out!

You can see the previous business card attached. It is a family run business in North Wales.

No individual names on the cards.

Key Things to Feature:
- The words "Prompt", "Local", "Reliable" (as you can see under the logo on the website)
- 24h Emergency Service
- Covering All of North Wales, the Wirral and Chester
- The color blue
- A key or a lock would be interesting (similar to the ones that come up when you google locksmith business card)

Optional (only if design includes bullet points, like the example below):
https://imgvaultcdn.net/samples/208314/55172/55172_3904821_208314_image.jpg
- Residential / Commercial / Automotive
- Alarms & Cameras
- Key Cutting & Safes

https://www.brynhafod-locksmiths.co.uk/

Industry/Entity Type

Locksmith

Contact Information for Business Card

01632 960 418
07700 900 362
brynhafodlocksmiths@mailvane.com
Brynhafod Locksmiths, The Willow Barn, 7 Tannery Rd., Llandudno LL99 4QX
www.brynhafod-locksmiths.co.uk

Requirements
Must have
• - The words "Prompt", "Local", "Reliable" (as you can see under the logo on the website)
• - 24h Emergency Service
• - Covering All of North Wales, the Wirral and Chester
Nice to have
• - A key or a lock would be interesting (similar to the ones that come up when you google locksmith business card)

```html
<!DOCTYPE html>
<html lang="en">
<head>
<meta charset="utf-8">
<title>Brynhafod Locksmiths – Business Cards</title>
<link rel="stylesheet" href="https://fonts.googleapis.com/css2?family=Oswald:wght@500&family=Roboto:wght@400&display=swap">
<style>
  :root {
    --backdrop: #3a3a3a;
    --navy-deep: #23275f;
    --navy: #2b2f72;
    --navy-light: #6d7dbd;
    --ink: #3c3c44;
    --paper: #ffffff;
  }
  * { box-sizing: border-box; margin: 0; padding: 0; }
  html, body { width: 1200px; height: 900px; overflow: hidden; }
  body {
    background: var(--backdrop);
    position: relative;
    font-family: "Roboto", Arial, sans-serif;
  }
  .card {
    position: absolute;
    width: 665px;
    height: 380px;
    border-radius: 2px;
    overflow: hidden;
    box-shadow: 0 10px 28px rgba(0,0,0,.45);
  }

  /* Front */
  .card-front {
    left: 420px; top: 45px;
    background: linear-gradient(120deg, var(--navy-deep) 0%, var(--navy) 40%, var(--navy-light) 100%);
    color: var(--paper);
    text-align: center;
  }
  .front-brand {
    position: absolute; left: 0; right: 0; top: 92px;
    font-family: "Oswald", Impact, sans-serif;
    font-weight: 500;
    font-size: 46px;
    line-height: 1;
    letter-spacing: 1px;
    text-transform: uppercase;
    color: var(--paper);
  }
  .front-tagline {
    position: absolute; left: 0; right: 0; top: 200px;
    font-size: 16px; line-height: 1.25;
  }
  .front-tagline .values { letter-spacing: 1.5px; text-transform: uppercase; }

  /* Back */
  .card-back {
    left: 120px; top: 470px;
    background: var(--paper);
    color: var(--ink);
  }
  .back-brand {
    position: absolute; left: 40px; top: 32px;
    font-family: "Oswald", Impact, sans-serif;
    font-weight: 500;
    font-size: 38px; line-height: 1;
    text-transform: uppercase;
    color: var(--navy);
  }
  .services {
    position: absolute; left: 40px; top: 122px;
    list-style: none;
    font-size: 17px; line-height: 1.3;
  }
  .divider {
    position: absolute; left: 40px; right: 40px; top: 208px;
    height: 1px; background: var(--navy);
  }
  .contacts {
    position: absolute; left: 40px; top: 228px;
    list-style: none;
    font-size: 19px; line-height: 1.45;
  }
  .contacts li { display: flex; align-items: center; gap: 9px; }
  .contacts svg { width: 17px; height: 17px; fill: var(--navy); flex: none; }
  .address {
    position: absolute; right: 40px; top: 226px;
    text-align: right;
    font-size: 19px; line-height: 1.4;
    color: var(--navy);
    font-style: normal;
  }
  .base-band {
    position: absolute; left: 0; right: 0; bottom: 0;
    height: 14px; background: var(--navy);
  }
</style>
</head>
<body>

<section class="card card-front">
  <h1 class="front-brand">Brynhafod<br>Locksmiths</h1>
  <p class="front-tagline">
    <span class="values">Prompt - Local - Reliable</span><br>
    24h Emergency Service<br>
    Covering All of North Wales, the Wirral and Chester
  </p>
</section>

<section class="card card-back">
  <h2 class="back-brand">Brynhafod<br>Locksmiths</h2>
  <ul class="services">
    <li>Residential | Commercial | Automotive</li>
    <li>Alarms &amp; Cameras</li>
    <li>Key Cutting &amp; Safes</li>
  </ul>
  <div class="divider"></div>
  <ul class="contacts">
    <li><svg viewBox="0 0 24 24" aria-hidden="true"><path d="M6.6 10.8a15 15 0 0 0 6.6 6.6l2.2-2.2a1 1 0 0 1 1-.25 11.4 11.4 0 0 0 3.6.57 1 1 0 0 1 1 1V20a1 1 0 0 1-1 1A17 17 0 0 1 3 4a1 1 0 0 1 1-1h3.5a1 1 0 0 1 1 1c0 1.25.2 2.45.57 3.57a1 1 0 0 1-.25 1z"/></svg>01632 960 418</li>
    <li><svg viewBox="0 0 24 24" aria-hidden="true"><path d="M6.6 10.8a15 15 0 0 0 6.6 6.6l2.2-2.2a1 1 0 0 1 1-.25 11.4 11.4 0 0 0 3.6.57 1 1 0 0 1 1 1V20a1 1 0 0 1-1 1A17 17 0 0 1 3 4a1 1 0 0 1 1-1h3.5a1 1 0 0 1 1 1c0 1.25.2 2.45.57 3.57a1 1 0 0 1-.25 1z"/></svg>07700 900 362</li>
    <li><svg viewBox="0 0 24 24" aria-hidden="true"><path d="M2 5h20v14H2z M3.5 6.5 12 12.5l8.5-6z" fill-rule="evenodd"/></svg>brynhafodlocksmiths@mailvane.com</li>
    <li><svg viewBox="0 0 24 24" aria-hidden="true"><path d="M12 2a10 10 0 1 0 0 20 10 10 0 0 0 0-20zm0 2c.9 1.2 1.7 2.9 2 5h-4c.3-2.1 1.1-3.8 2-5zM9.9 4.4A11 11 0 0 0 8 9H4.9a8 8 0 0 1 5-4.6zm4.2 0A8 8 0 0 1 19.1 9H16a11 11 0 0 0-1.9-4.6zM4.3 11H8v2H4.3a8 8 0 0 1 0-2zm5.7 0h4v2h-4zm6 0h3.7a8 8 0 0 1 0 2H16zM4.9 15H8a11 11 0 0 0 1.9 4.6A8 8 0 0 1 4.9 15zm5.1 0h4c-.3 2.1-1.1 3.8-2 5-.9-1.2-1.7-2.9-2-5zm6 0h3.1a8 8 0 0 1-5 4.6A11 11 0 0 0 16 15z"/></svg>www.brynhafod-locksmiths.co.uk</li>
  </ul>
  <address class="address">The Willow Barn, 7 Tannery Rd.<br>Llandudno LL99 4QX</address>
  <div class="base-band"></div>
</section>

</body>
</html>
```